Real Estate Company / Capital Needs Cards!

need business cards designed using the logos that were just designed by pixelbarn.

Reason: per designers request deadline extended 1 day…thank you.

Target Market(s)

Investors and clients looking to purchase real estate or invest in the business.

Industry/Entity Type

Business

Requirements
Must have
• two designs - one for the real estate logo and one for the capital logo, similar but slightly different.
Nice to have
• something to make it pop (perhaps on the back)
Should not have
• much color

```html
<!DOCTYPE html>
<html lang="en">
<head>
<meta charset="utf-8">
<title>Loma Real Estate – Business Cards</title>
<link rel="stylesheet" href="https://fonts.googleapis.com/css2?family=Open+Sans:wght@400;600&display=swap">
<style>
  :root {
    --bg: #e9e6e2;
    --card: #ffffff;
    --ink: #3a3a3a;
    --grey: #7b7b7d;
    --grey-light: #b4b4b6;
    --grey-faint: #ececec;
    --shadow: rgba(0, 0, 0, 0.18);
  }
  * { box-sizing: border-box; margin: 0; padding: 0; }
  html, body { width: 1200px; height: 498px; overflow: hidden; }
  body {
    background: var(--bg);
    font-family: "Open Sans", Arial, sans-serif;
    color: var(--ink);
    position: relative;
  }
  .card {
    position: absolute;
    top: 104px;
    width: 510px;
    height: 290px;
    background: var(--card);
    border-radius: 24px;
    box-shadow: 0 6px 18px var(--shadow);
    overflow: hidden;
  }
  .card--front { left: 50px; }
  .card--back { left: 640px; }

  .brand { position: absolute; display: flex; align-items: center; }
  .brand__square { background: var(--grey); border-radius: 4px; }
  .brand__name {
    font-weight: 400;
    color: var(--grey);
    text-transform: uppercase;
    line-height: 1.05;
  }

  .card--front .brand { left: 30px; top: 30px; gap: 14px; }
  .card--front .brand__square { width: 58px; height: 58px; }
  .card--front .brand__name { font-size: 22px; letter-spacing: 2px; }

  .card--back .brand { left: 90px; top: 98px; gap: 22px; }
  .card--back .brand__square { width: 96px; height: 96px; }
  .card--back .brand__name { font-size: 38px; letter-spacing: 3px; }

  .decor-square {
    position: absolute;
    right: 34px;
    top: 92px;
    width: 96px;
    height: 96px;
    border-radius: 10px;
    background: var(--grey-faint);
  }

  .holder {
    position: absolute;
    right: 34px;
    top: 196px;
    text-align: right;
  }
  .holder__name { font-size: 18px; font-weight: 600; color: var(--ink); }
  .holder__title { font-size: 14px; color: var(--grey); }

  .contacts {
    position: absolute;
    left: 36px;
    top: 176px;
    list-style: none;
    font-size: 15px;
    line-height: 1.55;
  }
  .contacts li { display: flex; align-items: center; gap: 6px; }
  .contacts .small { font-size: 13px; }
  .contacts svg { width: 12px; height: 12px; fill: var(--ink); }

  .website {
    position: absolute;
    left: 0;
    right: 0;
    top: 222px;
    text-align: center;
    font-size: 15px;
    letter-spacing: 3px;
    color: var(--ink);
  }
  .website strong { font-weight: 600; }
</style>
</head>
<body>
  <section class="card card--front">
    <div class="brand">
      <span class="brand__square"></span>
      <span class="brand__name">Loma<br>Real Estate</span>
    </div>
    <span class="decor-square"></span>
    <div class="holder">
      <p class="holder__name">Your Name</p>
      <p class="holder__title">Title</p>
    </div>
    <ul class="contacts">
      <li>
        <svg viewBox="0 0 12 12"><path d="M2 1h3l1 3-1.5 1a6 6 0 0 0 2.5 2.5L8 6l3 1v3a1 1 0 0 1-1 1A9 9 0 0 1 1 2a1 1 0 0 1 1-1z"/></svg>
        123-456-7980
      </li>
      <li>
        <svg viewBox="0 0 12 12"><path d="M3 1h6v3H3zM1 5h10v5H1zM3 8h6v3H3z"/></svg>
        123-568-7896
      </li>
      <li class="small">
        <svg viewBox="0 0 12 12"><path d="M1 3h10v7H1zM1 3l5 4 5-4"/></svg>
        hello@lomarealestate.com
      </li>
      <li class="small">Street Name, City Name State ZipCode</li>
    </ul>
  </section>

  <section class="card card--back">
    <div class="brand">
      <span class="brand__square"></span>
      <span class="brand__name">Loma<br>Real Estate</span>
    </div>
    <p class="website">www.<strong>lomarealestate</strong>.com</p>
  </section>
</body>
</html>
```